Boutique custom software development company needs new business card

Our nearly 20 year old custom software development company would like to better include the fact that we are now providing Bitcoin services. These new services are B2B include education (how to acquire and securely hold Bitcoin) and integrating Bitcoin payments into existing ecommerce sites or other existing systems. Please keep the card clean and simple. Attached is our current design and some other files. vextorial.com

Target Market(s)

businesses owners interested in long term relationship

Industry/Entity Type

Custom software development and Bitcoin

Contact Information for Business Card

Dale Parker, dale@vextorial.com, vextorial.com, (888) 555-VXTRL

Font styles to use
Other font styles liked:
• monospace

Requirements
Must have
• double-sided
Nice to have
• clean and simple
Should not have
• physical address

```html
<!DOCTYPE html>
<html lang="en">
<head>
<meta charset="utf-8">
<title>Vextorial – Business Card</title>
<link rel="stylesheet" href="https://fonts.googleapis.com/css2?family=Courier+Prime:wght@400;700&family=Open+Sans:wght@400;800&display=swap">
<style>
  :root {
    --bg: #e8e3da;
    --card: #ffffff;
    --blue: #3d72b9;
    --orange: #f07f22;
    --ink: #333333;
  }
  * { margin: 0; padding: 0; box-sizing: border-box; }
  html, body { width: 900px; height: 1200px; overflow: hidden; }
  body { background: var(--bg); position: relative; font-family: "Courier Prime", "Courier New", monospace; }

  .card {
    position: absolute;
    left: 80px;
    width: 742px;
    height: 440px;
    background: var(--card);
    border-radius: 38px;
  }
  .card--front { top: 132px; }
  .card--back { top: 638px; }

  /* Front */
  .brand-block {
    position: absolute;
    left: 104px;
    top: 76px;
    width: 276px;
    height: 288px;
    display: flex;
    flex-direction: column;
    align-items: center;
    justify-content: center;
    gap: 26px;
  }
  .brand-block__square { width: 150px; height: 150px; background: var(--blue); }
  .brand-block__name {
    font-family: "Courier Prime", "Courier New", monospace;
    font-weight: 700;
    font-size: 34px;
    color: var(--blue);
    letter-spacing: 1px;
  }
  .divider {
    position: absolute;
    left: 413px;
    top: 76px;
    width: 2px;
    height: 288px;
    background: var(--blue);
  }
  .contact {
    position: absolute;
    left: 443px;
    top: 90px;
    color: var(--ink);
    font-size: 15px;
  }
  .contact__name {
    color: var(--orange);
    font-size: 24px;
    font-weight: 400;
    letter-spacing: 1.5px;
    margin-bottom: 44px;
  }
  .contact__list { list-style: none; }
  .contact__item { display: flex; align-items: center; gap: 10px; height: 25px; }
  .contact__icon { width: 15px; height: 15px; fill: var(--orange); flex: none; }
  .services { list-style: none; margin-top: 45px; line-height: 25px; }

  /* Back */
  .wordmark {
    position: absolute;
    left: 42px;
    top: 120px;
    width: 660px;
    height: 132px;
  }
  .wordmark text {
    font-family: "Open Sans", Arial, sans-serif;
    font-weight: 800;
    font-size: 160px;
    fill: var(--blue);
  }
  .tagline {
    position: absolute;
    left: 0;
    right: 0;
    top: 266px;
    text-align: center;
    font-family: "Open Sans", Arial, sans-serif;
    font-size: 42px;
    letter-spacing: -1.3px;
    color: var(--blue);
  }
</style>
</head>
<body>
  <section class="card card--front">
    <div class="brand-block">
      <div class="brand-block__square"></div>
      <div class="brand-block__name">Vextorial</div>
    </div>
    <div class="divider"></div>
    <div class="contact">
      <h1 class="contact__name">DALE PARKER</h1>
      <ul class="contact__list">
        <li class="contact__item">
          <svg class="contact__icon" viewBox="0 0 16 16" aria-hidden="true"><path d="M1 5c0-2 3-3 7-3s7 1 7 3v1h-4V4.8C10 4.4 9 4.3 8 4.3s-2 .1-3 .5V6H1z"/><path d="M4 7h8l2 7H2z"/></svg>
          <span>(888) 555-VXTRL</span>
        </li>
        <li class="contact__item">
          <svg class="contact__icon" viewBox="0 0 16 16" aria-hidden="true"><path d="M1 4h14v1L8 9 1 5z"/><path d="M1 6.5l7 4 7-4V13H1z"/></svg>
          <span>dale@vextorial.com</span>
        </li>
        <li class="contact__item">
          <svg class="contact__icon" viewBox="0 0 16 16" aria-hidden="true"><circle cx="8" cy="8" r="7"/><path d="M4 4c2 0 2 2 4 2s0 3-2 3-1 3-2 3" stroke="#fff" stroke-width="1.4" fill="none"/></svg>
          <span>www.vextorial.com</span>
        </li>
      </ul>
      <ul class="services">
        <li>Custom Software</li>
        <li>Bitcoin Payments</li>
        <li>Bitcoin Education</li>
      </ul>
    </div>
  </section>

  <section class="card card--back">
    <svg class="wordmark" viewBox="0 0 660 132" aria-label="Vextorial">
      <text x="0" y="126" textLength="656" lengthAdjust="spacingAndGlyphs">VEXTORIAL</text>
    </svg>
    <p class="tagline">developer of custom applications</p>
  </section>
</body>
</html>
```